Young, dynamic furniture company needs a new business card design

We require a new business card design for our modern furniture company which supplies furniture and appliances to the property and development market.
Oakridge Interiors has become one of the leading furniture & appliance suppliers to the property market withing London. With over 10 years experience, we have increased our business to supply not only private landlords and managing agents, but also property developers, housing associations and local councils.
We offer not only a complete range of furniture which includes beds, wardrobes, dining sets and sofas, but also a high quality, full delivery and assembly service to help you with all our furnishing needs.

Target Market(s)

Private landlords, estate agents, letting agents, property management companies

Industry/Entity Type

Business

Contact Information for Business Card

Name,
Title,
Address,
Mobile,
Telephone,
Fax, Website, email address

Font styles to use
Sans Serif

Colors
3176b5
0555a3
85abd2
cfdeed

Requirements
Must have
• All the above information for each of our staff, along with our logo

```html
<!DOCTYPE html>
<html lang="en">
<head>
<meta charset="utf-8">
<title>Oakridge Interiors – Business Card</title>
<link rel="stylesheet" href="https://fonts.googleapis.com/css2?family=Montserrat:wght@400;500;700&display=swap">
<style>
  :root {
    --bg: #e9e6e1;
    --navy: #1f3a6e;
    --accent: #1f6fb5;
    --white: #ffffff;
    --frost-a: #eef0f1;
    --frost-b: #d9dcdf;
    --ink: #2b2b2b;
    --ink-soft: #4a4a4a;
  }
  html, body {
    margin: 0;
    width: 1200px;
    height: 902px;
    overflow: hidden;
    background: var(--bg);
    font-family: "Montserrat", Arial, sans-serif;
  }
  .card {
    position: absolute;
    left: 80px;
    top: 155px;
    width: 1040px;
    height: 593px;
    box-shadow: 0 10px 30px rgba(0,0,0,0.18);
  }
  .card-shapes {
    position: absolute;
    inset: 0;
  }
  .person {
    position: absolute;
    left: 63px;
    top: 108px;
    color: var(--white);
  }
  .person-name {
    margin: 0;
    font-size: 35px;
    font-weight: 700;
    line-height: 1;
    letter-spacing: 0.5px;
  }
  .person-title {
    margin: 2px 0 0;
    font-size: 24px;
    font-weight: 500;
    line-height: 1.1;
  }
  .address {
    position: absolute;
    left: 63px;
    top: 243px;
    margin: 0;
    color: var(--white);
    font-size: 25px;
    font-weight: 400;
    line-height: 38px;
    font-style: normal;
  }
  .contacts {
    position: absolute;
    left: 63px;
    top: 328px;
    margin: 0;
    padding: 0;
    list-style: none;
    color: var(--white);
  }
  .contact {
    display: flex;
    align-items: center;
    height: 37px;
    font-size: 25px;
  }
  .contact-icon {
    width: 30px;
    height: 30px;
    margin-right: 14px;
    flex: none;
  }
  .brand {
    position: absolute;
    left: 560px;
    top: 362px;
    width: 440px;
    text-align: center;
  }
  .brand-name {
    display: inline-flex;
    align-items: center;
    gap: 12px;
    margin: 0;
    color: var(--ink);
    font-size: 34px;
    font-weight: 500;
    letter-spacing: 0.5px;
    text-transform: uppercase;
  }
  .brand-mark {
    width: 22px;
    height: 22px;
    background: var(--accent);
  }
  .brand-tagline {
    margin: 8px 0 0;
    color: var(--ink-soft);
    font-size: 17px;
    font-weight: 400;
    letter-spacing: 1px;
    text-transform: uppercase;
  }
</style>
</head>
<body>
  <section class="card">
    <svg class="card-shapes" width="1040" height="593" viewBox="0 0 1040 593">
      <defs>
        <linearGradient id="frost" x1="0" y1="0" x2="1" y2="1">
          <stop offset="0" stop-color="#e6e8ea"/>
          <stop offset="0.5" stop-color="#f3f4f5"/>
          <stop offset="1" stop-color="#d6d9dc"/>
        </linearGradient>
      </defs>
      <rect class="frost-panel" width="1040" height="593" fill="url(#frost)"/>
      <polygon class="white-strip" points="380,0 454,0 612,593 598,593" fill="var(--white)"/>
      <line class="accent-line" x1="456" y1="0" x2="614" y2="593" stroke="var(--accent)" stroke-width="3"/>
      <polygon class="navy-panel" points="0,0 393,0 600,593 0,593" fill="var(--navy)"/>
    </svg>

    <div class="person">
      <h1 class="person-name">DANIEL REEVE</h1>
      <p class="person-title">Manager</p>
    </div>

    <address class="address">
      Your Address, 2nd Ste<br>
      Maple Grove, Texas 1234, USA
    </address>

    <ul class="contacts">
      <li class="contact">
        <svg class="contact-icon" viewBox="0 0 30 30" aria-label="Telephone"><rect width="30" height="30" fill="#fff"/><path d="M10 6 L13 6 L14 11 L12 13 Q14 18 18 19 L20 17 L24 18 L24 22 Q23 24 20 24 Q9 22 7 10 Q7 7 10 6Z" fill="var(--navy)"/></svg>
        123 456 7890
      </li>
      <li class="contact">
        <svg class="contact-icon" viewBox="0 0 30 30" aria-label="Fax"><rect width="30" height="30" fill="#fff"/><rect x="9" y="6" width="12" height="6" fill="var(--navy)"/><rect x="5" y="12" width="20" height="9" rx="1" fill="var(--navy)"/><rect x="9" y="18" width="12" height="7" fill="var(--navy)" stroke="#fff" stroke-width="1.5"/></svg>
        123 456 7890
      </li>
      <li class="contact">
        <svg class="contact-icon" viewBox="0 0 30 30" aria-label="Mobile"><rect width="30" height="30" fill="#fff"/><rect x="9" y="4" width="12" height="22" rx="2" fill="var(--navy)"/><rect x="11" y="7" width="8" height="9" fill="#fff"/></svg>
        123 456 7890
      </li>
      <li class="contact">
        <svg class="contact-icon" viewBox="0 0 30 30" aria-label="Email"><rect width="30" height="30" fill="#fff"/><rect x="5" y="8" width="20" height="14" fill="none" stroke="var(--navy)" stroke-width="2"/><path d="M5 8 L15 16 L25 8" fill="none" stroke="var(--navy)" stroke-width="2"/></svg>
        your@yourcompany.com
      </li>
      <li class="contact">
        <svg class="contact-icon" viewBox="0 0 30 30" aria-label="Website"><rect width="30" height="30" fill="#fff"/><g fill="none" stroke="var(--navy)" stroke-width="1.6"><circle cx="15" cy="15" r="10"/><ellipse cx="15" cy="15" rx="4.5" ry="10"/><line x1="5" y1="15" x2="25" y2="15"/><line x1="7" y1="10" x2="23" y2="10"/><line x1="7" y1="20" x2="23" y2="20"/></g></svg>
        www.yourcompany.com
      </li>
    </ul>

    <div class="brand">
      <p class="brand-name"><span class="brand-mark"></span>Oakridge Interiors</p>
      <p class="brand-tagline">Trade Furniture Solutions</p>
    </div>
  </section>
</body>
</html>
```